MEDICAL CLINIC LETTERHEAD

Design is a letterhead for a non-profit medical center. The name of the clinic is VITARIDGE Community Health Center. Although the full name must be included, the community health center part is more of a description and should be less visible - i attached an example of what I mean by that (ATTACHED IMAGE IS AN EXAMPLE OF FONT SIZES NOT A DESIGN IDEA). Please design something modern, cool looking and unique because I can always download free templates.
Phone, email, website and etc will be added later.

Industry/Entity Type

MEDICAL

```html
<!DOCTYPE html>
<html lang="en">
<head>
<meta charset="utf-8">
<title>VITARIDGE Community Health Center – Letterhead</title>
<link rel="stylesheet" href="https://fonts.googleapis.com/css2?family=Lato:wght@400;700&family=Dancing+Script:wght@600&display=swap">
<style>
  :root {
    --navy: #16254a;
    --gold: #b4955a;
    --ink: #2b2b2b;
    --paper: #ffffff;
    --backdrop: #dcdcdc;
  }
  * { box-sizing: border-box; margin: 0; padding: 0; }
  html, body {
    width: 1200px; height: 874px; overflow: hidden;
    background: var(--backdrop);
    font-family: "Lato", sans-serif;
    color: var(--ink);
  }
  .letterhead {
    position: absolute; left: 306px; top: 22px;
    width: 587px; height: 830px;
    background: var(--paper);
    overflow: hidden;
  }
  .brand {
    position: absolute; left: 40px; top: 58px;
    display: flex; align-items: center; gap: 8px;
  }
  .brand__square { width: 14px; height: 14px; background: var(--gold); }
  .brand__name {
    font-weight: 700; font-size: 26px; letter-spacing: 1px; color: var(--navy);
  }
  .contact {
    position: absolute; right: 36px; top: 40px;
    border-left: 1px solid var(--gold);
    padding-left: 10px;
    font-size: 8.5px; line-height: 1.45; color: #111;
  }
  .contact__org { margin-bottom: 3px; }
  .contact__row { display: flex; align-items: center; gap: 6px; }
  .contact__row svg { width: 8px; height: 8px; fill: var(--gold); }
  .letter {
    position: absolute; left: 48px; top: 160px; width: 470px;
    font-size: 9.5px; line-height: 1.35;
  }
  .letter__date, .letter__recipient, .letter__address { margin-bottom: 12px; font-size: 10.5px; }
  .letter__greeting { font-weight: 700; font-size: 12px; margin-bottom: 10px; }
  .letter p { margin-bottom: 14px; }
  .letter__closing { margin-top: 24px; font-size: 10px; }
  .letter__signature {
    font-family: "Dancing Script", cursive;
    font-size: 30px; color: #222; margin: 6px 0 0 40px;
  }
  .wave { position: absolute; left: 0; top: 0; width: 587px; height: 830px; }
</style>
</head>
<body>
  <main class="letterhead">
    <div class="brand">
      <span class="brand__square"></span>
      <span class="brand__name">VITARIDGE</span>
    </div>

    <address class="contact" style="font-style:normal">
      <div class="contact__org">VITARIDGE Community<br>Health Center</div>
      <div class="contact__row">
        <svg viewBox="0 0 10 10"><path d="M2 0h2l1 3-1.5 1a6 6 0 0 0 2.5 2.5L7 5l3 1v2c0 1-1 2-2 2C4 10 0 6 0 2c0-1 1-2 2-2z"/></svg>555-210-4821
      </div>
      <div class="contact__row">
        <svg viewBox="0 0 10 10"><path d="M0 2h10v6H0z M0 2l5 3.5L10 2" /></svg>hello@vitaridge-mail.com
      </div>
      <div class="contact__row">
        <svg viewBox="0 0 10 10"><circle cx="5" cy="5" r="5"/></svg>www.vitaridge-web.com
      </div>
    </address>

    <article class="letter">
      <div class="letter__date">Feb-03-2022</div>
      <div class="letter__recipient">Mr. Peter Lane<br>President</div>
      <div class="letter__address">Northway Group<br>48 Harbor Road, Suite# 12<br>Lakeview, State, 240117</div>
      <div class="letter__greeting">Dear Mr, Peter</div>
      <p>Lorem ipsum dolor sit amet, consectetur adipisicing elit, sed do eiusmod tempor incididunt ut labore et dolore magna aliqua. Ut enim ad minim veniam, quis nostrud exercitation ullamco laboris nisi ut aliquip ex ea commodo consequat. Duis aute irure dolor in reprehenderit in voluptate velit esse cillum dolore eu fugiat nulla pariatur.</p>
      <p>Lorem ipsum dolor sit amet, consectetur adipisicing elit, sed do eiusmod tempor incididunt ut labore et dolore magna aliqua. Ut enim ad minim veniam, quis nostrud exercitation ullamco laboris nisi ut aliquip ex ea commodo consequat. Duis aute irure dolor in reprehenderit in voluptate velit esse cillum dolore eu fugiat nulla pariatur.</p>
      <p>Lorem ipsum dolor sit amet, consectetur adipisicing elit, sed do eiusmod tempor incididunt ut labore et dolore magna aliqua. Ut enim ad minim veniam, quis nostrud exercitation ullamco laboris nisi ut aliquip ex ea commodo consequat.</p>
      <p>Excepteur sint occaecat cupidatat non proident, sunt in culpa qui officia deserunt mollit anim id est laborum. re et dolore magnam aliquam quaerat voluptatem.</p>
      <div class="letter__closing">Regards</div>
      <div class="letter__signature">Daniel Hart</div>
    </article>

    <svg class="wave" viewBox="0 0 587 830" aria-hidden="true">
      <path fill="var(--gold)" d="M0 812 C150 790 230 770 330 745 C430 720 500 710 587 708 L587 830 L0 830 Z"/>
      <path fill="var(--navy)" d="M0 800 C140 775 230 752 320 730 C420 706 500 700 566 700 C500 704 420 712 325 738 C230 762 140 788 0 808 Z"/>
      <path fill="var(--gold)" d="M0 797 C150 770 240 740 330 722 C420 704 490 694 587 692 L587 695 C490 697 420 708 330 726 C240 744 150 774 0 800 Z"/>
    </svg>
  </main>
</body>
</html>
```